Construction Company Cellar Crafters needs Business Card

I would like modern looking business card design. I am attaching logo of our company. Please include cell nr 302.418.7650 , email address cellarcrafters4u@examplemail.com, web : cellarcrafters4u.com, please also include wording: Specializing in finishing and remodeling basements. You can play with dark grey and orange colors or any ideas are welcome. Also include social media icons Friendloop and HouseGuidr.

```html
<!DOCTYPE html>
<html lang="en">
<head>
<meta charset="utf-8">
<title>Cellar Crafters – Business Card</title>
<link href="https://fonts.googleapis.com/css2?family=Open+Sans:wght@400;600;700&display=swap" rel="stylesheet">
<style>
  :root {
    --page-bg: #e8e5e2;
    --card-bg: #1f2a35;
    --accent: #f07a3a;
    --text-light: #ffffff;
  }
  * { box-sizing: border-box; margin: 0; padding: 0; }
  html, body { width: 1200px; height: 900px; overflow: hidden; }
  body {
    position: relative;
    background: var(--page-bg);
    font-family: "Open Sans", Arial, sans-serif;
  }
  .card {
    position: absolute;
    background: var(--card-bg);
    box-shadow: 0 6px 18px rgba(0,0,0,0.25);
  }
  .card-front { left: 238px; top: 62px; width: 555px; height: 342px; }
  .card-back  { left: 459px; top: 519px; width: 559px; height: 342px; }

  .brand-name-front {
    position: absolute;
    left: 32px; top: 112px; width: 228px;
    text-align: center;
    color: var(--text-light);
    font-weight: 700;
    font-size: 26px;
    line-height: 1.15;
    letter-spacing: 0.5px;
  }
  .person-name {
    position: absolute; left: 272px; top: 84px;
    color: var(--accent); font-weight: 600; font-size: 17px;
  }
  .person-role {
    position: absolute; left: 272px; top: 106px;
    color: var(--text-light); font-size: 14px;
  }
  .contact-list {
    position: absolute; left: 272px; top: 154px;
    list-style: none;
  }
  .contact-list li {
    display: flex; align-items: center; gap: 8px;
    color: var(--text-light); font-size: 14px;
    height: 20px;
  }
  .contact-list svg { width: 11px; height: 11px; fill: var(--text-light); flex: none; }
  .social-list {
    position: absolute; left: 274px; top: 230px;
    display: flex; gap: 14px; list-style: none;
  }
  .social-list li {
    display: flex; align-items: center; gap: 5px;
    color: var(--text-light); font-size: 12px;
  }
  .social-list .dot { width: 12px; height: 12px; background: var(--accent); }
  .tagline {
    position: absolute; left: 0; right: 0; top: 294px;
    text-align: center;
    color: var(--accent); font-size: 14px; letter-spacing: 0.2px;
  }

  .brand-name-back {
    position: absolute; left: 0; right: 0; top: 150px;
    text-align: center;
    color: var(--accent);
    font-weight: 700;
    font-size: 40px;
    letter-spacing: 2px;
    text-transform: uppercase;
  }
</style>
</head>
<body>
  <section class="card card-front">
    <div class="brand-name-front">Cellar<br>Crafters</div>
    <div class="person-name">Daniel Brooks</div>
    <div class="person-role">Managing Director</div>
    <ul class="contact-list">
      <li><svg viewBox="0 0 24 24"><path d="M6.6 10.8a15.1 15.1 0 0 0 6.6 6.6l2.2-2.2c.3-.3.7-.4 1-.2 1.1.4 2.3.6 3.6.6.6 0 1 .4 1 1V20c0 .6-.4 1-1 1A17 17 0 0 1 3 4c0-.6.4-1 1-1h3.5c.6 0 1 .4 1 1 0 1.3.2 2.5.6 3.6.1.3 0 .7-.2 1z"/></svg>302.418.7650</li>
      <li><svg viewBox="0 0 24 24"><path d="M2 5h20v14H2z M2 5l10 8 10-8" fill="none" stroke="#fff" stroke-width="2"/><path d="M2 6l10 7 10-7v13H2z"/></svg>cellarcrafters4u@examplemail.com</li>
      <li><svg viewBox="0 0 24 24"><circle cx="12" cy="12" r="10"/></svg>cellarcrafters4u.com</li>
    </ul>
    <ul class="social-list">
      <li><span class="dot"></span>Friendloop</li>
      <li><span class="dot"></span>HouseGuidr</li>
    </ul>
    <p class="tagline">SPECIALIZING IN FINISHING AND REMODELING BASEMENTS.</p>
  </section>

  <section class="card card-back">
    <div class="brand-name-back">Cellar Crafters</div>
  </section>
</body>
</html>
```